Professional & attention grabbing.

A business card design, front and back. I already have a logo I will attach, but I am open to something new as well.
Things to include:
Name:
Title:
Phone:
Email:
Wanting something that is professional but attention grabbing.
Also we do a lot of work using drones on natural gas pipelines (leading the future)if you want to include any of that. I'm open to ideas.
Target Market(s)
Natural gas transmission industry / greenhouse gas mitigation industry
Industry/Entity Type
Business
Colors
Designer to choose colors to be used in the design.
Look and feel
Each slider illustrates characteristics of the customer's brand and the style your logo design should communicate.

```html
<!DOCTYPE html>
<html lang="en">
<head>
<meta charset="utf-8">
<title>Ridgeline Inspections – Business Card</title>
<link rel="stylesheet" href="https://fonts.googleapis.com/css2?family=Michroma&family=Roboto:wght@400;500;700;900&display=swap">
<style>
  :root {
    --backdrop: #4b4b4d;
    --card-dark: #2a2a2c;
    --card-dark-2: #3a3a3d;
    --card-light: #f6f6f6;
    --accent-red: #d8211f;
    --ink-light: #ffffff;
    --ink-muted: #d6d6d6;
    --ink-dark: #3b3b3d;
  }
  * { box-sizing: border-box; margin: 0; padding: 0; }
  html, body {
    width: 1200px; height: 852px; overflow: hidden;
    background: var(--backdrop);
    font-family: "Roboto", Arial, sans-serif;
  }
  .stage {
    position: relative; width: 1200px; height: 852px;
    display: flex; align-items: center; justify-content: center; gap: 60px;
  }
  .card {
    position: relative; width: 520px; height: 300px;
    border-radius: 18px; overflow: hidden;
    box-shadow: 0 14px 30px rgba(0,0,0,0.35);
  }

  /* Front */
  .card--front {
    background: linear-gradient(135deg, var(--card-dark-2) 0%, var(--card-dark) 60%, #222224 100%);
  }
  .front__brand {
    position: absolute; left: 0; right: 0; top: 82px;
    display: flex; align-items: center; justify-content: center; gap: 14px;
  }
  .brand-mark {
    width: 26px; height: 26px; background: var(--accent-red);
  }
  .brand-name {
    font-weight: 900; font-size: 40px; letter-spacing: 0.5px;
    color: var(--ink-light); line-height: 1;
  }
  .front__band {
    position: absolute; left: 0; right: 0; top: 200px; height: 32px;
    background: var(--accent-red);
    display: flex; align-items: center; justify-content: center;
    color: var(--ink-light); font-size: 15px; font-weight: 400; letter-spacing: 0.2px;
  }

  /* Back */
  .card--back { background: linear-gradient(135deg, var(--card-dark-2) 0%, var(--card-dark) 70%); }
  .back__panel { position: absolute; inset: 0; }
  .back__brand {
    position: absolute; right: 34px; top: 118px;
    display: flex; align-items: center; gap: 10px;
  }
  .back__brand .brand-name { color: var(--ink-dark); font-size: 30px; }
  .back__brand .brand-mark { width: 20px; height: 20px; }
  .person {
    position: absolute; left: 40px; top: 108px; color: var(--ink-light);
  }
  .person__name {
    font-family: "Michroma", "Arial Black", sans-serif;
    font-size: 19px; letter-spacing: 1px;
  }
  .person__title { font-size: 12px; color: var(--ink-muted); margin-top: 4px; }
  .contacts {
    position: absolute; left: 40px; bottom: 36px; list-style: none;
    color: var(--ink-light); font-size: 13px; line-height: 21px;
  }
  .contacts li { display: flex; align-items: center; gap: 10px; }
  .contacts svg { width: 13px; height: 13px; fill: var(--ink-light); flex: none; }
</style>
</head>
<body>
<main class="stage">

  <section class="card card--front" aria-label="Business card front">
    <div class="front__brand">
      <span class="brand-mark"></span>
      <span class="brand-name">Ridgeline Inspections</span>
    </div>
    <div class="front__band">Also we do a lot of work using drones on natural gas pipelines</div>
  </section>

  <section class="card card--back" aria-label="Business card back">
    <svg class="back__panel" viewBox="0 0 520 300" preserveAspectRatio="none" aria-hidden="true">
      <path d="M520 0 L250 0 C210 60 200 190 320 300 L520 300 Z" fill="var(--card-light)"/>
      <path d="M262 0 C222 70 214 180 318 300 L306 300 C196 190 206 70 248 0 Z" fill="var(--accent-red)"/>
    </svg>
    <div class="back__brand">
      <span class="brand-mark"></span>
      <span class="brand-name">Ridgeline</span>
    </div>
    <div class="person">
      <p class="person__name">DANIEL HART</p>
      <p class="person__title">Managing Director</p>
    </div>
    <ul class="contacts">
      <li>
        <svg viewBox="0 0 24 24"><path d="M6.6 10.8a15.1 15.1 0 0 0 6.6 6.6l2.2-2.2c.3-.3.7-.4 1-.2 1.1.4 2.3.6 3.6.6.6 0 1 .4 1 1V20c0 .6-.4 1-1 1C10.6 21 3 13.4 3 4c0-.6.4-1 1-1h3.5c.6 0 1 .4 1 1 0 1.3.2 2.5.6 3.6.1.3 0 .7-.2 1z"/></svg>
        1300 480 512
      </li>
      <li>
        <svg viewBox="0 0 24 24"><path d="M12 2a10 10 0 1 0 0 20 10 10 0 0 0 0-20zm6.9 6h-2.9a15.6 15.6 0 0 0-1.4-3.6A8 8 0 0 1 18.9 8zM12 4c.8 1.2 1.5 2.5 1.9 4h-3.8c.4-1.5 1.1-2.8 1.9-4zM4.3 14a8 8 0 0 1 0-4h3.4a16 16 0 0 0 0 4zm.8 2h2.9c.3 1.3.8 2.5 1.4 3.6A8 8 0 0 1 5.1 16zM8 8H5.1a8 8 0 0 1 4.3-3.6C8.8 5.5 8.3 6.7 8 8zm4 12c-.8-1.2-1.5-2.5-1.9-4h3.8c-.4 1.5-1.1 2.8-1.9 4zm2.3-6H9.7a14.7 14.7 0 0 1 0-4h4.6a14.7 14.7 0 0 1 0 4zm.3 5.6c.6-1.1 1.1-2.3 1.4-3.6h2.9a8 8 0 0 1-4.3 3.6zm1.7-5.6a16 16 0 0 0 0-4h3.4a8 8 0 0 1 0 4z"/></svg>
        www.ridgelineinspect.com
      </li>
      <li>
        <svg viewBox="0 0 24 24"><path d="M2 5h20v14H2zm2 2v.5l8 5 8-5V7zm0 2.8V17h16V9.8l-8 5z"/></svg>
        daniel.hart@ridgelineinspect.com
      </li>
    </ul>
  </section>

</main>
</body>
</html>
```